Bref créative
business cards and stationary set
Zumvo Business cards and stationary
Bright & Fun-filled
Mirela Dostanik
Marketing Manager
4217 Harrowbend Blvd,
Suite 352
Larkwell, NV, 75841
mirela@zumvopeak.com
www.zumvopeak.com
Logo
picture
picture 2

```html
<!DOCTYPE html>
<html lang="en">
<head>
<meta charset="UTF-8">
<title>Zumvo Business Card</title>
<link href="https://fonts.googleapis.com/css2?family=Open+Sans:ital,wght@0,400;0,600;0,700;1,600;1,700&display=swap" rel="stylesheet">
<style>
  :root {
    --backdrop: #3a3a3a;
    --card-dark: #0c0c0c;
    --card-mid: #1c1c1c;
    --accent: #39e61e;
    --ink-light: #ffffff;
    --ink-soft: #d6d6d6;
    --swoosh: #e9e9e9;
  }
  * { margin: 0; padding: 0; box-sizing: border-box; }
  html, body {
    width: 1200px; height: 780px; overflow: hidden;
    background: var(--backdrop);
    font-family: "Open Sans", Arial, sans-serif;
  }
  .card {
    position: absolute; left: 100px; top: 105px;
    width: 1000px; height: 570px;
    border-radius: 30px; overflow: hidden;
    background: radial-gradient(ellipse at 30% 40%, var(--card-mid) 0%, var(--card-dark) 70%);
  }
  .card-swoosh { position: absolute; inset: 0; }
  .brand {
    position: absolute; left: 40px; top: 150px; width: 400px;
    text-align: center;
  }
  .brand-rule {
    height: 3px;
    background: linear-gradient(90deg, transparent, var(--accent) 25%, var(--accent) 75%, transparent);
  }
  .brand-name {
    font-weight: 700; font-size: 104px; line-height: 1;
    color: var(--ink-light); letter-spacing: 2px;
    padding: 16px 0 18px;
  }
  .brand-domain {
    margin-top: 16px;
    font-size: 21px; font-weight: 600; letter-spacing: 9px;
    color: var(--ink-light);
  }
  .details { position: absolute; left: 560px; top: 72px; color: var(--ink-light); }
  .person-name { font-size: 30px; font-weight: 700; font-style: italic; color: var(--accent); line-height: 1.15; }
  .person-title { font-size: 20px; font-weight: 600; font-style: italic; color: var(--ink-light); margin-top: 2px; }
  .address { margin-top: 26px; font-size: 19px; line-height: 1.4; color: var(--ink-soft); }
  .contacts { list-style: none; margin-top: 24px; }
  .contacts li {
    display: flex; align-items: center; gap: 12px;
    font-size: 19px; line-height: 1; color: var(--ink-soft);
    height: 34px;
  }
  .contact-icon { width: 22px; height: 22px; flex: none; }
</style>
</head>
<body>
  <div class="card">
    <svg class="card-swoosh" viewBox="0 0 1000 570" preserveAspectRatio="none" aria-hidden="true">
      <path d="M0 425 C 180 385, 380 440, 560 470 C 740 498, 900 470, 1000 440 L1000 570 L0 570 Z" fill="var(--swoosh)"/>
      <path d="M0 462 C 200 440, 400 490, 600 505 C 780 518, 920 500, 1000 478 L1000 570 L0 570 Z" fill="var(--accent)"/>
    </svg>

    <div class="brand">
      <div class="brand-rule"></div>
      <div class="brand-name">Zumvo</div>
      <div class="brand-rule"></div>
      <div class="brand-domain">ZUMVOPEAK.COM</div>
    </div>

    <div class="details">
      <div class="person-name">Mirela Dostanik</div>
      <div class="person-title">Marketing Manager</div>
      <div class="address">4217 Harrowbend Blvd,<br>Suite 352, Larkwell, NV, 75841</div>
      <ul class="contacts">
        <li>
          <svg class="contact-icon" viewBox="0 0 24 24"><path fill="var(--accent)" d="M6.6 10.8a15 15 0 0 0 6.6 6.6l2.2-2.2c.3-.3.7-.4 1-.2 1.1.4 2.3.6 3.6.6.6 0 1 .4 1 1V20c0 .6-.4 1-1 1A17 17 0 0 1 3 4c0-.6.4-1 1-1h3.5c.6 0 1 .4 1 1 0 1.3.2 2.5.6 3.6.1.3 0 .7-.2 1z"/></svg>
          555-304-1862
        </li>
        <li>
          <svg class="contact-icon" viewBox="0 0 24 24"><rect x="7" y="2" width="10" height="20" rx="2" fill="var(--accent)"/><rect x="9" y="5" width="6" height="11" fill="var(--card-dark)"/></svg>
          555-718-2436
        </li>
        <li>
          <svg class="contact-icon" viewBox="0 0 24 24"><rect x="3" y="9" width="18" height="11" rx="2" fill="var(--accent)"/><rect x="7" y="3" width="10" height="7" fill="var(--accent)"/><rect x="7" y="13" width="10" height="2" fill="var(--card-dark)"/></svg>
          555-304-1879
        </li>
        <li>
          <svg class="contact-icon" viewBox="0 0 24 24"><circle cx="12" cy="12" r="10" fill="var(--accent)"/><rect x="6.5" y="8" width="11" height="8" fill="var(--card-dark)"/><path d="M6.5 8 L12 12.5 L17.5 8" stroke="var(--accent)" stroke-width="1.4" fill="none"/></svg>
          mirela@zumvopeak.com
        </li>
        <li>
          <svg class="contact-icon" viewBox="0 0 24 24"><circle cx="12" cy="12" r="10" fill="var(--accent)"/><circle cx="12" cy="12" r="6" fill="none" stroke="var(--card-dark)" stroke-width="1.5"/><path d="M6 12h12M12 6c-3 3-3 9 0 12M12 6c3 3 3 9 0 12" stroke="var(--card-dark)" stroke-width="1.3" fill="none"/></svg>
          www.zumvopeak.com
        </li>
      </ul>
    </div>
  </div>
</body>
</html>
```